Working Capital graphics

Our business advisory firm requires 9 images to be re-created and improved in the branding of our business.

The 9 images have been uploaded below and the colours and branding of the business can be found at the website www.tallowmereadvisory.com.au

```html
<!DOCTYPE html>
<html lang="en">
<head>
<meta charset="utf-8">
<title>Inventories – Inventory Drivers</title>
<link rel="stylesheet" href="https://fonts.googleapis.com/css2?family=Figtree:ital,wght@0,500;0,600;1,700;1,800&display=swap">
<style>
  :root {
    --page: #ffffff;
    --panel: #55a8de;
    --line: #ffffff;
    --box: #ffffff;
    --ink: #111111;
    --accent: #f39c42;
    --header: #eaf4fb;
  }
  html, body {
    margin: 0;
    padding: 0;
    width: 1200px;
    height: 1000px;
    overflow: hidden;
    background: var(--page);
    font-family: "Figtree", "Helvetica Neue", Arial, sans-serif;
  }
  .canvas {
    position: relative;
    width: 1200px;
    height: 1000px;
  }
  .panel {
    position: absolute;
    left: 54px;
    top: 61px;
    width: 1099px;
    height: 878px;
    background: var(--panel);
  }
  .connectors {
    position: absolute;
    left: 0;
    top: 0;
    width: 1200px;
    height: 1000px;
  }
  .connectors path {
    stroke: var(--line);
    stroke-width: 2;
    fill: none;
  }
  .title {
    position: absolute;
    left: 120px;
    top: 140px;
    margin: 0;
    font-size: 35px;
    font-style: italic;
    font-weight: 800;
    color: var(--line);
    letter-spacing: 0.2px;
  }
  .column-label {
    position: absolute;
    top: 160px;
    margin: 0;
    font-size: 17px;
    font-weight: 600;
    color: var(--header);
    transform: translateX(-50%);
    white-space: nowrap;
  }
  .column-label--group { left: 566px; }
  .column-label--sub { left: 913px; }

  .root-box {
    position: absolute;
    left: 120px;
    top: 449px;
    width: 205px;
    height: 108px;
    background: var(--box);
    display: flex;
    align-items: center;
    justify-content: center;
    text-align: center;
    font-size: 20px;
    line-height: 1.25;
    font-style: italic;
    font-weight: 700;
    color: var(--ink);
  }
  .driver {
    position: absolute;
    left: 452px;
    width: 213px;
    height: 43px;
    background: var(--box);
    display: flex;
    align-items: center;
    justify-content: center;
    font-size: 18px;
    font-style: italic;
    font-weight: 700;
    color: var(--ink);
  }
  .driver__number {
    position: absolute;
    left: -27px;
    top: 50%;
    width: 54px;
    height: 54px;
    margin-top: -27px;
    border-radius: 50%;
    background: var(--accent);
    color: var(--line);
    display: flex;
    align-items: center;
    justify-content: center;
    font-size: 30px;
    font-weight: 800;
    font-style: italic;
    letter-spacing: -2px;
  }
  .driver__name { padding-left: 2px; }
  .sub {
    position: absolute;
    left: 729px;
    width: 336px;
    height: 30px;
    margin-top: -15px;
    background: var(--box);
    display: flex;
    align-items: center;
    justify-content: center;
    font-size: 16px;
    font-style: italic;
    font-weight: 700;
    color: var(--ink);
    white-space: nowrap;
  }
</style>
</head>
<body>
<div class="canvas">
  <div class="panel"></div>

  <svg class="connectors" viewBox="0 0 1200 1000" aria-hidden="true">
    <path d="M343 502 H398 M398 297 V783 M398 297 H452 M398 475 H452 M398 626 H452 M398 783 H452"/>
    <path d="M665 296 H697 M697 218 V372 M697 218 H729 M697 269 H729 M697 321 H729 M697 372 H729"/>
    <path d="M665 476 H697 M697 425 V527 M697 425 H729 M697 476 H729 M697 527 H729"/>
    <path d="M665 627 H697 M697 580 V674 M697 580 H729 M697 627 H729 M697 674 H729"/>
    <path d="M665 784 H697 M697 735 V837 M697 735 H729 M697 784 H729 M697 837 H729"/>
  </svg>

  <h1 class="title">Inventories</h1>
  <p class="column-label column-label--group">Driver Group</p>
  <p class="column-label column-label--sub">Sub-groups</p>

  <div class="root-box">Inventory<br>Drivers</div>

  <div class="driver" style="top:274px"><span class="driver__number">10</span><span class="driver__name">Planning</span></div>
  <div class="driver" style="top:454px"><span class="driver__number">11</span><span class="driver__name">Procurement</span></div>
  <div class="driver" style="top:605px"><span class="driver__number">12</span><span class="driver__name">Fulfilment</span></div>
  <div class="driver" style="top:762px"><span class="driver__number">13</span><span class="driver__name">Product Range</span></div>

  <div class="sub" style="top:218px">Demand variability</div>
  <div class="sub" style="top:269px">Planning collaboration</div>
  <div class="sub" style="top:321px">Information availability</div>
  <div class="sub" style="top:372px">Inventory target setting</div>

  <div class="sub" style="top:425px">Order quantities</div>
  <div class="sub" style="top:476px">Supplier lead time variability</div>
  <div class="sub" style="top:527px">Supplier quality variability</div>

  <div class="sub" style="top:580px">Customer service leads</div>
  <div class="sub" style="top:627px">Network structure</div>
  <div class="sub" style="top:674px">Supplier quality variability</div>

  <div class="sub" style="top:735px">Customer service leads</div>
  <div class="sub" style="top:784px">Parts standardisation</div>
  <div class="sub" style="top:837px">SKU proliferation</div>
</div>
</body>
</html>
```